Velk Partners Building Business Cards

We need a business card that reflects our business as "Solar Experts" in San Diego. Browse our website www.velkpartners.example our License needs to be displayed as "CSLB# 3867140" our phone number is (619) 555-0187

Save thousands on your electric bills and increase the value of your home while helping to protect the environment. Our solar installation experts will help you design the system that's right for you, using only the highest quality equipment that will look great and give you ideal performance. Our goal is to make you energy independent, and get your electric bill to 0.

Paul Osterby
(619) 555-0187
paul@velkpartners.example

Target Market(s)

Home owners in san diego looking for solar

Industry/Entity Type

Solar Energy

Contact Information for Business Card

Paul Osterby
(619) 555-0187
paul@velkpartners.example

Font styles to use
Other font styles liked:
• Use our logo font

Requirements
Must have
• License needs to be displayed as "CSLB# 3867140" our phone number is (619) 555-0187
Nice to have
• Real images of rooftop home solar in san diego
Should not have
• our business address

```html
<!DOCTYPE html>
<html lang="en">
<head>
<meta charset="utf-8">
<title>Velk Partners Building – Business Card</title>
<link rel="stylesheet" href="https://fonts.googleapis.com/css2?family=Poppins:wght@700&family=Tinos:wght@400;700&display=swap">
<style>
  :root {
    --brand-blue: #2457a8;
    --brand-blue-dark: #1b4588;
    --solar-yellow: #f5c518;
    --text-white: #ffffff;
    --page-bg: #e8e6e2;
  }
  * { box-sizing: border-box; margin: 0; padding: 0; }
  html, body { width: 1200px; height: 780px; overflow: hidden; }
  body {
    background: var(--page-bg);
    position: relative;
    font-family: "Tinos", "Times New Roman", serif;
  }
  .card {
    position: absolute;
    top: 235px;
    width: 540px;
    height: 309px;
    border-radius: 16px;
    overflow: hidden;
    box-shadow: 0 6px 18px rgba(0,0,0,0.18);
  }
  .card--front { left: 40px; background: var(--brand-blue); }
  .card--back { left: 620px; }
  .card__art { position: absolute; inset: 0; width: 100%; height: 100%; }

  .wordmark {
    font-family: "Poppins", "Arial", sans-serif;
    font-weight: 700;
    line-height: 1.02;
    letter-spacing: -0.5px;
    display: flex;
    align-items: center;
    gap: 8px;
  }
  .wordmark__sun {
    width: 16px; height: 16px; border-radius: 50%;
    background: var(--solar-yellow);
    flex: none;
  }
  .card--front .wordmark {
    position: absolute; left: 22px; top: 92px;
    font-size: 28px; color: var(--brand-blue);
  }

  .contact {
    position: absolute; right: 26px; top: 34px;
    text-align: right; color: var(--text-white);
  }
  .contact__name { font-weight: 700; font-size: 21px; margin-bottom: 6px; margin-right: 28px; }
  .contact__line {
    display: flex; justify-content: flex-end; align-items: center;
    gap: 8px; font-size: 15px; line-height: 22px;
  }
  .contact__icon {
    width: 18px; height: 18px; border-radius: 4px;
    background: var(--solar-yellow);
    display: inline-flex; align-items: center; justify-content: center;
  }
  .license {
    position: absolute; left: 120px; bottom: 16px;
    font-size: 15px; color: var(--text-white);
  }
  .license__label { color: var(--solar-yellow); }

  .card--back .wordmark {
    position: absolute; left: 0; right: 0; top: 96px;
    justify-content: center; text-align: center;
    font-size: 40px; color: var(--text-white);
  }
  .card--back .wordmark__sun { width: 22px; height: 22px; }
  .social {
    position: absolute; left: 0; right: 0; top: 222px;
    display: flex; justify-content: center; gap: 10px;
  }
  .social__tile {
    width: 18px; height: 18px; border-radius: 3px;
    background: var(--text-white);
  }
</style>
</head>
<body>

<section class="card card--front" aria-label="Business card front">
  <svg class="card__art" viewBox="0 0 540 309" aria-hidden="true">
    <defs>
      <linearGradient id="front-blue" x1="0" y1="0" x2="1" y2="1">
        <stop offset="0" stop-color="#2f67bf"/>
        <stop offset="1" stop-color="#1f4f9e"/>
      </linearGradient>
      <linearGradient id="panel-fill" x1="0" y1="0" x2="1" y2="1">
        <stop offset="0" stop-color="#f1f2f4"/>
        <stop offset="1" stop-color="#d3d6da"/>
      </linearGradient>
    </defs>
    <rect width="540" height="309" fill="url(#front-blue)"/>
    <polygon points="0,0 340,0 222,242 0,278" fill="#f5c518"/>
    <polygon points="0,0 328,0 218,234 0,270" fill="#2457a8"/>
    <polygon points="0,0 315,0 213,224 0,256" fill="url(#panel-fill)" role="img" aria-label="Photo of rooftop solar panels"/>
  </svg>

  <div class="wordmark"><span>Velk Partners<br>Building</span><span class="wordmark__sun"></span></div>

  <div class="contact">
    <p class="contact__name">Paul Osterby</p>
    <p class="contact__line">(619) 555-0187
      <span class="contact__icon"><svg width="12" height="12" viewBox="0 0 12 12"><path d="M2.5 1.5l2 0 1 2.5-1.3 1a6 6 0 0 0 2.8 2.8l1-1.3 2.5 1v2a1 1 0 0 1-1 1A9 9 0 0 1 1.5 2.5a1 1 0 0 1 1-1z" fill="#1b4588"/></svg></span>
    </p>
    <p class="contact__line">paul@velkpartners.example
      <span class="contact__icon"><svg width="12" height="12" viewBox="0 0 12 12"><rect x="1" y="2.5" width="10" height="7" fill="none" stroke="#1b4588" stroke-width="1.3"/><path d="M1 2.5l5 4 5-4" fill="none" stroke="#1b4588" stroke-width="1.3"/></svg></span>
    </p>
    <p class="contact__line">www.velkpartners.example
      <span class="contact__icon"><svg width="12" height="12" viewBox="0 0 12 12"><circle cx="6" cy="6" r="4.7" fill="none" stroke="#1b4588" stroke-width="1.2"/><ellipse cx="6" cy="6" rx="2" ry="4.7" fill="none" stroke="#1b4588" stroke-width="1"/><path d="M1.3 6h9.4" stroke="#1b4588" stroke-width="1"/></svg></span>
    </p>
  </div>

  <p class="license"><span class="license__label">License:</span> CSLB# 3867140</p>
</section>

<section class="card card--back" aria-label="Business card back">
  <svg class="card__art" viewBox="0 0 540 309" role="img" aria-label="Blue-toned photo of solar panels">
    <defs>
      <linearGradient id="back-blue" x1="0" y1="0" x2="1" y2="1">
        <stop offset="0" stop-color="#3a6cbc"/>
        <stop offset="0.55" stop-color="#2a5aa8"/>
        <stop offset="1" stop-color="#1d4689"/>
      </linearGradient>
    </defs>
    <rect width="540" height="309" fill="url(#back-blue)"/>
  </svg>

  <div class="wordmark"><span>Velk Partners<br>Building</span><span class="wordmark__sun"></span></div>

  <div class="social" aria-label="Social links">
    <span class="social__tile"></span>
    <span class="social__tile"></span>
    <span class="social__tile"></span>
    <span class="social__tile"></span>
  </div>
</section>

</body>
</html>
```